Modern Business Card for Larkwell 2018

Our company assumes the best about people. We are creating an online community of entrepreneurs and business leaders who struggle with marketing their business online.

This business card should POP! We recently got a new logo and are launching a new website next month, so our business cards should make a statement that feels:
-Fresh
-Smart
-Trustworthy
-Fun

Target Market(s)

small business owners, entrepreneurs

Industry/Entity Type

Digital Marketing

Contact Information for Business Card

Dimensions: 3.5" x 2"

Font styles to use
Sans Serif

Colors
f37122
ffffff

Requirements
Must have
• We need a business card with a modern, bold design. We will use one side of the card as a lead-generation offer, so text on one side will need to fit up to 140 characters. The business card should stick to our core colors (orange, black, and white).
Nice to have
• We think a vertical "portrait" design could be interesting.
Should not have
• Should not look like a traditional business card. The round icon should stand out from a distance.

```html
<!DOCTYPE html>
<html lang="en">
<head>
<meta charset="utf-8">
<title>Larkwell Business Card</title>
<link href="https://fonts.googleapis.com/css2?family=Roboto:wght@400;500;700;900&family=Yellowtail&display=swap" rel="stylesheet">
<style>
  :root {
    --orange: #f26a25;
    --black: #000000;
    --white: #ffffff;
    --paper: #f1f1f1;
    --backdrop: #e6e2dd;
  }
  html, body {
    margin: 0;
    padding: 0;
    width: 1200px;
    height: 960px;
    overflow: hidden;
    background: var(--backdrop);
    font-family: "Roboto", Arial, sans-serif;
  }
  .card {
    position: absolute;
    width: 342px;
    height: 600px;
    border-radius: 18px;
    overflow: hidden;
  }
  .card-front { left: 262px; top: 163px; background: var(--paper); }
  .card-back { left: 621px; top: 165px; background: var(--orange); }

  .front-curve { position: absolute; left: 0; top: 0; width: 342px; height: 600px; }

  .brand-mark {
    position: absolute; left: 0; width: 100%;
    display: flex; flex-direction: column; align-items: center;
  }
  .front-brand { top: 58px; gap: 14px; }
  .brand-dot { border-radius: 50%; background: var(--orange); }
  .front-brand .brand-dot { width: 72px; height: 72px; }
  .front-brand .brand-name {
    color: var(--orange); font-weight: 900; font-size: 34px; letter-spacing: 1px;
  }

  .person { position: absolute; left: 0; top: 383px; width: 100%; text-align: center; color: var(--white); }
  .person-role { margin: 0; font-size: 14.5px; font-weight: 500; letter-spacing: .4px; line-height: 18px; }
  .person-name { margin: 18px 0 0; font-family: "Yellowtail", "Brush Script MT", cursive; font-weight: 400; font-size: 48px; line-height: 50px; }
  .person-email { margin: 20px 0 0; font-size: 15.5px; font-weight: 700; line-height: 18px; }

  .offer-headline {
    position: absolute; left: 0; top: 70px; width: 100%; margin: 0;
    text-align: center; color: var(--white);
    font-size: 18px; font-weight: 700; line-height: 25px; text-transform: uppercase;
  }
  .offer-band {
    position: absolute; left: 0; top: 226px; width: 100%; height: 148px;
    background: var(--black); color: var(--white);
  }
  .offer-copy { position: absolute; left: 81px; top: 28px; margin: 0; font-size: 14.5px; line-height: 19.5px; }
  .offer-link { position: absolute; left: 0; top: 94px; width: 100%; margin: 0; text-align: center; font-size: 18.5px; font-weight: 700; }

  .back-brand { top: 422px; gap: 8px; color: var(--white); }
  .back-brand .brand-dot { width: 36px; height: 36px; background: var(--white); }
  .back-brand .brand-name { font-size: 42px; font-weight: 900; letter-spacing: 1px; line-height: 1; margin-top: 4px; }
  .back-brand .brand-tagline { font-size: 11px; font-weight: 700; letter-spacing: 1px; text-transform: uppercase; margin-top: 2px; }
</style>
</head>
<body>
  <section class="card card-front">
    <svg class="front-curve" viewBox="0 0 342 600" aria-hidden="true">
      <path d="M0 330 C60 260 282 240 342 340" fill="none" stroke="var(--orange)" stroke-width="6"/>
      <path d="M0 340 C60 272 282 252 342 350 L342 600 L0 600 Z" fill="var(--black)"/>
    </svg>
    <div class="brand-mark front-brand">
      <span class="brand-dot"></span>
      <span class="brand-name">Larkwell</span>
    </div>
    <div class="person">
      <p class="person-role">STORY MARKETING COACH</p>
      <p class="person-name">Dana Whitfield</p>
      <p class="person-email">dana@larkwellnow.com</p>
    </div>
  </section>

  <section class="card card-back">
    <p class="offer-headline">Grow your audience.<br>Earn what you're worth.<br>Leave a bigger mark.</p>
    <div class="offer-band">
      <p class="offer-copy">Get your free Larkwell<br>Starter Package and our<br>marketing guide today at</p>
      <p class="offer-link">Larkwellnow.com/start</p>
    </div>
    <div class="brand-mark back-brand">
      <span class="brand-dot"></span>
      <span class="brand-name">LARKWELL</span>
      <span class="brand-tagline">Share stories that move people</span>
    </div>
  </section>
</body>
</html>
```